Brantor Works Business Card

Modern and Professional Business Card for a Med size construction/development company.

See the samples below for the design I like … but I need ideas for incorporating the red company logo while still keeping the clean look of the card samples that are attached.

Logo and tag line on the back … info on the front.

Tagline: Built Right from the First Footing

Target Market(s)

Med-Large General Contractors

Contact Information for Business Card

Brantor Works Limited
42 Fenwick Avenue
Harrow Bay, NL
A9X 2K4

t: 709-555-0147
f: 709-555-0182
w: www.brantorworks-example.com

Font styles to use
Sans Serif

Colors
fbee3e

Requirements
Must have
• I like the black and yellow designs of the attached samples …. but I'm not sure how to incorporate the red Brantor Works logo into that design??
Nice to have
• Construction safety strips

```html
<!DOCTYPE html>
<html lang="en">
<head>
<meta charset="utf-8">
<title>Brantor Works Business Card</title>
<link rel="stylesheet" href="https://fonts.googleapis.com/css2?family=Montserrat:wght@400;500;700;800&display=swap">
<style>
  :root {
    --safety-yellow: #fbee3e;
    --panel-yellow: #e2dc3a;
    --card-black: #262626;
    --brand-red: #d8262c;
    --text-white: #f2f2f2;
    --text-dark: #1d1d1d;
    --page-bg: #d9d9d9;
  }
  * { box-sizing: border-box; margin: 0; padding: 0; }
  html, body { width: 1200px; height: 1021px; overflow: hidden; }
  body {
    background: var(--page-bg);
    font-family: "Montserrat", sans-serif;
    position: relative;
  }
  .card {
    position: absolute;
    left: 200px;
    width: 800px;
    height: 457px;
    background: var(--card-black);
    overflow: hidden;
    box-shadow: 0 10px 28px rgba(0,0,0,0.35);
  }
  .card--back { top: 36px; }
  .card--front { top: 528px; }

  .hazard-band {
    position: absolute;
    background: repeating-linear-gradient(
      -60deg,
      var(--safety-yellow) 0 34px,
      transparent 34px 78px
    );
  }
  .card--back .hazard-band { left: 0; right: 0; top: 150px; height: 112px; }

  .brand {
    position: absolute;
    left: 50%;
    top: 140px;
    transform: translateX(-50%);
    width: 370px;
    height: 132px;
    background: var(--card-black);
    display: flex;
    align-items: center;
    justify-content: center;
    gap: 16px;
  }
  .brand__mark { width: 34px; height: 34px; background: var(--brand-red); }
  .brand__name {
    font-weight: 800;
    font-size: 36px;
    color: var(--text-white);
    letter-spacing: 0.5px;
  }
  .tagline {
    position: absolute;
    top: 290px;
    width: 100%;
    text-align: center;
    color: var(--text-white);
    font-weight: 700;
    font-size: 19px;
  }

  .card--front .hazard-band--top { left: 0; right: 0; top: 18px; height: 36px; }
  .card--front .hazard-band--bottom { left: 0; right: 0; top: 392px; height: 40px; }

  .name-panel {
    position: absolute;
    left: 0; top: 0;
    width: 800px; height: 457px;
  }
  .holder {
    position: absolute;
    left: 44px;
    top: 170px;
    color: var(--text-dark);
  }
  .holder__name { font-weight: 700; font-size: 27px; }
  .holder__role { font-weight: 400; font-size: 18px; margin-top: 2px; }

  .contact {
    position: absolute;
    color: var(--text-white);
    font-size: 17px;
    line-height: 1.3;
  }
  .contact--address { left: 440px; top: 112px; }
  .contact--lines { left: 440px; top: 294px; list-style: none; }
  .contact li, .contact--address { display: flex; gap: 12px; align-items: flex-start; }
  .contact svg { flex: 0 0 16px; width: 16px; height: 16px; margin-top: 3px; fill: var(--safety-yellow); }
</style>
</head>
<body>

<section class="card card--back" aria-label="Card back">
  <div class="hazard-band"></div>
  <div class="brand">
    <span class="brand__mark"></span>
    <span class="brand__name">Brantor Works</span>
  </div>
  <p class="tagline">Built Right from the First Footing</p>
</section>

<section class="card card--front" aria-label="Card front">
  <div class="hazard-band hazard-band--top"></div>
  <div class="hazard-band hazard-band--bottom"></div>
  <svg class="name-panel" viewBox="0 0 800 457" aria-hidden="true">
    <polygon points="0,72 320,72 372,290 0,290" fill="var(--card-black)"/>
    <polygon points="0,80 312,80 362,282 0,282" fill="var(--panel-yellow)"/>
    <line x1="362" y1="282" x2="770" y2="282" stroke="var(--safety-yellow)" stroke-width="1.5"/>
  </svg>

  <div class="holder">
    <p class="holder__name">Daniel Whitcombe</p>
    <p class="holder__role">Founder / Owner</p>
  </div>

  <div class="contact contact--address">
    <svg viewBox="0 0 16 16"><path d="M8 0a5.5 5.5 0 0 0-5.5 5.5C2.5 10 8 16 8 16s5.5-6 5.5-10.5A5.5 5.5 0 0 0 8 0zm0 8a2.5 2.5 0 1 1 0-5 2.5 2.5 0 0 1 0 5z"/></svg>
    <p>Brantor Works Limited<br>42 Fenwick Avenue<br>Harrow Bay, NL<br>A9X 2K4</p>
  </div>

  <ul class="contact contact--lines">
    <li><svg viewBox="0 0 16 16"><path d="M3.5 0 6 3.5 4.5 5.5c1 2.3 3.2 4.5 5.5 5.5L12 9.5l3.5 2.5-1.5 3C8 15 1 8 1 1.5z"/></svg>709-555-0147</li>
    <li><svg viewBox="0 0 16 16"><path d="M4 1h8v4H4zM1 6h14v6h-3v3H4v-3H1zm4 4v4h6v-4z"/></svg>709-555-0182</li>
    <li><svg viewBox="0 0 16 16"><path d="M0 3h16v10H0zm1.5 1.2v.4L8 9l6.5-4.4v-.4zM1.5 6.4v5.1h13V6.4L8 10.8z"/></svg>info@brantorworks-example.com</li>
    <li><svg viewBox="0 0 16 16"><path d="M8 0a8 8 0 1 0 0 16A8 8 0 0 0 8 0zm5.9 7.2h-2.5a12 12 0 0 0-1-4.8 6.5 6.5 0 0 1 3.5 4.8zM8 1.6c.8 1 1.5 3 1.6 5.6H6.4C6.5 4.6 7.2 2.6 8 1.6zM5.6 2.4a12 12 0 0 0-1 4.8H2.1a6.5 6.5 0 0 1 3.5-4.8zM2.1 8.8h2.5a12 12 0 0 0 1 4.8 6.5 6.5 0 0 1-3.5-4.8zM8 14.4c-.8-1-1.5-3-1.6-5.6h3.2c-.1 2.6-.8 4.6-1.6 5.6zm2.4-.8a12 12 0 0 0 1-4.8h2.5a6.5 6.5 0 0 1-3.5 4.8z"/></svg>www.brantorworks-example.com</li>
  </ul>
</section>

</body>
</html>
```